Linden Medical - Flyer

We are a full service pharmacy that specializes in diabetic testing and medications. We research the patient's insurance to maximize their insurance benefit and then deliver the medications monthly directly to the patient's doorstep, for free! We save the patient, time and money every month.
We would love a flyer that we can distribute to Doctor's offices and patients that sum up our pharmacy. Emphasis on saving money, time, and getting the best quality supplies by maximizing their insurance. We want it to be eye catching, clean, and professional.
You can use our logo or feel free to make your own design.
diabetic patients wanting to save money
Insurance

```html
<!DOCTYPE html>
<html lang="en">
<head>
<meta charset="utf-8">
<title>Linden Medical – Flyer</title>
<link rel="stylesheet" href="https://fonts.googleapis.com/css2?family=Roboto+Condensed:wght@400;700&family=Roboto:wght@300;400&display=swap">
<style>
  :root{
    --bg:#ecece8;
    --paper:#ffffff;
    --green:#8fb34a;
    --green-light:#b3cf7c;
    --green-pale:#e3ead9;
    --mint:#d6ddd6;
    --slate:#4a4a4c;
    --text:#3c3c3c;
    --orange:#f7891e;
    --photo-warm:#c9b8a2;
    --photo-cool:#cfd8db;
  }
  *{box-sizing:border-box;margin:0;padding:0}
  html,body{width:1200px;height:805px;overflow:hidden;background:var(--bg)}
  body{position:relative;font-family:"Roboto Condensed",Arial,sans-serif;color:var(--text)}
  .page{position:absolute;top:45px;width:548px;height:705px;background:var(--paper);box-shadow:0 2px 10px rgba(0,0,0,.18);overflow:hidden}
  .page--front{left:33px}
  .page--back{left:613px}
  .abs{position:absolute}

  .hero{left:0;top:0;width:100%;height:300px;background:linear-gradient(180deg,#dfe5df,var(--mint))}
  .photo{background:linear-gradient(135deg,var(--photo-warm),#e8dfd2)}
  .photo--cool{background:linear-gradient(135deg,var(--photo-cool),#eef1ee)}

  .brand-box{background:var(--green-pale)}
  .brand{display:flex;align-items:center;gap:9px;font-family:"Roboto",Arial,sans-serif;font-weight:300;color:#6b6b6b;font-size:24px;letter-spacing:1px;white-space:nowrap}
  .brand::before{content:"";width:14px;height:14px;background:var(--green);flex:none}

  .tag-big{color:var(--orange);font-weight:700;font-size:58px;line-height:1}
  .tag-sub{color:var(--slate);font-weight:700;font-size:21px;line-height:1.15;text-align:center}

  .swoosh{left:0;width:100%}

  .lead{color:var(--orange);font-weight:700;font-size:25px;line-height:1.3;white-space:nowrap}
  .framed{border:4px solid #fff;box-shadow:0 1px 5px rgba(0,0,0,.3)}
  .copy{font-family:"Roboto",Arial,sans-serif;font-size:12.2px;line-height:1.3;color:#333;white-space:nowrap}

  .footer{left:0;bottom:0;width:100%;height:48px;background:linear-gradient(180deg,var(--green-light),var(--green));display:flex;align-items:center;justify-content:space-between;padding:0 20px;color:#fff;font-size:12px;font-weight:700}
  .footer span{display:flex;align-items:center;gap:6px}
  .footer svg{fill:#fff}

  .question{color:var(--slate);font-weight:700;line-height:1.08;text-transform:uppercase;white-space:nowrap}
  .question .q-small{font-size:21px}
  .question .q-orange{font-size:21px;color:var(--orange)}
  .question .q-big{font-size:36px;letter-spacing:.5px}

  .badge{right:-4px;top:278px;width:128px;height:128px}
  .badge-text{position:absolute;inset:0;display:flex;flex-direction:column;align-items:center;justify-content:center;color:#fff;font-weight:700;transform:rotate(18deg);line-height:1}
  .badge-text .amount{font-size:26px}
  .badge-text .label{font-size:16px}
  .badge-text .small{font-size:12px;font-weight:400}

  .benefits{left:20px;top:372px;width:510px}
  .benefit{display:flex;gap:16px;margin-bottom:14px}
  .benefit-icon{width:50px;height:50px;flex:none;fill:var(--green)}
  .benefit h3{color:var(--orange);font-size:18px;font-weight:700;text-transform:uppercase;margin-bottom:4px}
  .benefit h3 em{font-style:normal;text-transform:none}
  .benefit ul{list-style:none;font-family:"Roboto",Arial,sans-serif;font-size:11.4px;color:#333;line-height:1.35}
  .benefit li::before{content:"●";font-size:8px;margin-right:5px;vertical-align:1px}
</style>
</head>
<body>

<!-- FRONT -->
<section class="page page--front">
  <div class="abs hero"></div>
  <div class="abs photo" style="left:0;top:30px;width:305px;height:270px" role="img" aria-label="Smiling senior couple embracing"></div>
  <div class="abs brand-box" style="left:308px;top:0;width:240px;height:278px"></div>
  <div class="abs brand" style="left:322px;top:60px">LINDEN MEDICAL</div>
  <div class="abs" style="left:308px;top:140px;width:240px;text-align:center">
    <div class="tag-big">We save</div>
    <div class="tag-sub" style="margin-top:14px">THE PATIENT, TIME AND<br>MONEY EVERY MONTH</div>
  </div>

  <svg class="abs swoosh" style="top:270px" width="548" height="100" viewBox="0 0 548 100">
    <polygon points="0,8 548,30 548,50 0,50" fill="#9dbd57"/>
    <polygon points="0,50 548,50 548,70 0,92" fill="#4a4a4c"/>
    <polygon points="0,92 548,70 548,100 0,100" fill="#ffffff"/>
  </svg>

  <p class="abs lead" style="left:18px;top:366px">We are a pharmacy that specializes in diabetic<br>testing supplies and diabetic oral medications.</p>

  <div class="abs framed photo--cool" style="left:18px;top:443px;width:245px;height:150px" role="img" aria-label="Pharmacists in white coats at a pharmacy counter"></div>
  <div class="abs framed photo--cool" style="left:281px;top:443px;width:248px;height:150px;background:linear-gradient(135deg,#bfcbd6,#f1eee9)" role="img" aria-label="Hands testing blood sugar with a glucose meter"></div>

  <p class="abs copy" style="left:20px;top:601px">Give us a call or fill out our online form and we do the rest. We research your insurance<br>to maximize your benefits. Once we know what will save you the most, we contact your<br>physician, get the correct prescription, then your order arrives at your doorstep.</p>

  <footer class="abs footer">
    <span><svg width="10" height="14" viewBox="0 0 10 14"><path d="M2 0h2l1 4-2 1q1 3 3 4l1-2 3 1v2q-1 4-5 2Q0 9 0 3 0 0 2 0z"/></svg>(855) 555-0148</span>
    <span><svg width="13" height="13" viewBox="0 0 14 14"><circle cx="7" cy="7" r="6" fill="none" stroke="#fff" stroke-width="1.3"/><path d="M1 7h12M7 1v12" stroke="#fff" stroke-width="1"/></svg>www.lindenmedical.net</span>
    <span><svg width="15" height="11" viewBox="0 0 15 11"><rect width="15" height="11"/><path d="M0 0l7.5 6L15 0" stroke="#8fb34a" fill="none"/></svg>cs@lindenmedical.net</span>
  </footer>
</section>

<!-- BACK -->
<section class="page page--back">
  <div class="abs hero"></div>
  <div class="abs photo--cool" style="left:262px;top:0;width:286px;height:300px;background:linear-gradient(135deg,#dfe6e2,#c8d3cc)" role="img" aria-label="Smiling pharmacist holding a clipboard"></div>
  <div class="abs brand-box" style="left:7px;top:0;width:258px;height:278px;background:#e4ecd3"></div>
  <div class="abs brand" style="left:18px;top:60px">LINDEN MEDICAL</div>
  <div class="abs question" style="left:15px;top:128px">
    <div class="q-small">Are the costs of your</div>
    <div class="q-orange">Diabetic testing supplies</div>
    <div class="q-big" style="margin-top:4px">As high as your<br>blood sugar?</div>
  </div>

  <svg class="abs swoosh" style="top:270px" width="548" height="100" viewBox="0 0 548 100">
    <polygon points="0,8 548,30 548,50 0,50" fill="#9dbd57"/>
    <polygon points="0,50 548,50 548,70 0,92" fill="#4a4a4c"/>
    <polygon points="0,92 548,70 548,100 0,100" fill="#ffffff"/>
  </svg>

  <div class="abs badge">
    <svg width="128" height="128" viewBox="0 0 128 128">
      <polygon fill="#6fa63a" stroke="#fff" stroke-width="2" points="64,2 72,16 86,6 89,22 105,17 102,33 119,34 110,48 125,55 112,65 124,77 108,82 115,97 98,98 100,115 85,109 80,125 68,114 58,127 51,112 37,121 35,105 19,108 24,92 8,86 19,74 5,64 19,55 9,42 25,38 21,22 38,24 38,8 53,17"/>
    </svg>
    <div class="badge-text">
      <span class="amount">$20</span>
      <span class="label">GIFT CARD</span>
      <span class="small">of your choice</span>
      <span class="small">with your</span>
      <span class="small">first order</span>
    </div>
  </div>

  <div class="abs benefits">
    <div class="benefit">
      <svg class="benefit-icon" viewBox="0 0 50 50"><rect x="6" y="20" width="38" height="26"/><rect x="3" y="13" width="44" height="9"/><rect x="23" y="13" width="4" height="33" fill="#fff"/><path d="M25 13c-6-10-16-8-12-2 2 2 8 2 12 2zm0 0c6-10 16-8 12-2-2 2-8 2-12 2z"/></svg>
      <div>
        <h3>Free meter and gift card</h3>
        <ul><li>We get you the meter that is right for you</li><li>With your first order, receive a $20 gift card from Brightmart, Shopwise, or ValueCo</li></ul>
      </div>
    </div>
    <div class="benefit">
      <svg class="benefit-icon" viewBox="0 0 50 50"><circle cx="25" cy="25" r="22"/><circle cx="25" cy="25" r="17" fill="#fff"/><text x="25" y="33" text-anchor="middle" font-family="Roboto Condensed,sans-serif" font-weight="700" font-size="24" fill="#8fb34a">$</text></svg>
      <div>
        <h3>Save money</h3>
        <ul><li>We research your insurance to maximize your benefits</li><li>Save on out-of-pocket costs with every fill</li></ul>
      </div>
    </div>
    <div class="benefit">
      <svg class="benefit-icon" viewBox="0 0 50 50"><circle cx="11" cy="9" r="6"/><circle cx="39" cy="9" r="6"/><circle cx="25" cy="27" r="19"/><circle cx="25" cy="27" r="14" fill="#fff"/><path d="M25 17v11h7" stroke="#8fb34a" stroke-width="3" fill="none"/><path d="M12 43l-4 5M38 43l4 5" stroke="#8fb34a" stroke-width="3"/></svg>
      <div>
        <h3>Save time</h3>
        <ul><li>Never wait in line again</li><li>No driving to the pharmacy to get your prescription</li></ul>
      </div>
    </div>
    <div class="benefit">
      <svg class="benefit-icon" viewBox="0 0 50 50"><rect x="2" y="12" width="30" height="24"/><path d="M34 20h8l6 8v8H34z"/><circle cx="11" cy="39" r="5" stroke="#fff" stroke-width="2"/><circle cx="40" cy="39" r="5" stroke="#fff" stroke-width="2"/></svg>
      <div>
        <h3>Free delivery <em>right to your door</em></h3>
        <ul><li>Never forget to pick up your prescription</li><li>Your order arrives at your doorstep every month</li></ul>
      </div>
    </div>
  </div>

  <footer class="abs footer">
    <span><svg width="10" height="14" viewBox="0 0 10 14"><path d="M2 0h2l1 4-2 1q1 3 3 4l1-2 3 1v2q-1 4-5 2Q0 9 0 3 0 0 2 0z"/></svg>(855) 555-0148</span>
    <span><svg width="13" height="13" viewBox="0 0 14 14"><circle cx="7" cy="7" r="6" fill="none" stroke="#fff" stroke-width="1.3"/><path d="M1 7h12M7 1v12" stroke="#fff" stroke-width="1"/></svg>www.lindenmedical.net</span>
    <span><svg width="15" height="11" viewBox="0 0 15 11"><rect width="15" height="11"/><path d="M0 0l7.5 6L15 0" stroke="#8fb34a" fill="none"/></svg>cs@lindenmedical.net</span>
  </footer>
</section>

</body>
</html>
```